IT consulting company looking for a modern business design for a website and a new logo

We are the IT-consulting company VelmaTrix from Germany and need a new and modern business website and a new logo. We are specialized in output management. Our services include business analysis, outsourcing, development, training and project leading. We wish for a design with nature pictures (mountains, lakes, rivers, forests, etc.) for our company with the colors green and blue. If it is possible, a slow-mo video of a nature scene. The design should be responsive and the menu should change to a hamburger menu. The following are: • Services / Solutions 1. Output Management 2. Outsourcing 3. Development 4. Business Analyst 5. Training • Partners • Careers • About Us 1. Project A 2. Project B 3. Project C • Contact Notes for the following categories: For "Services / Solutions" we want to conclude some contents from all the sub-points and sub-points below. Additionally, we would like to see some sub-point under "Services / Solutions". For Output Management: "5 Benefits of Output Management Systems (OMS) - OMS Simplifies and Accelerates External Communication - Helps Reduce Communication Mistakes - Provides Customers With Fast and Secure Responses to your questions - Employees can focus on the essential as they can access prepared templates - Companies get complete transparency about their communication "The point" partner does not have sub-points. The content here is a quote and the logo from the company Brel. For now, just placeholders on this site. The next point wants to be "career" without sub-point and wants to contain some text. Carrer options wants to be listed here. Next point wants to be "About us", where we need sub-points which we do not know exactly at this moment, but they will contain text. By clicking directly on "About us" we want to include pictures and texts about 6 employees for which we only need placeholders at the moment. The last point wants to be "contact", where customers can send us messages. The main page should include a story about our company, which can be a placeholder for now. For reference, designs have a look at: https://brelvanto.de/ https://www.tarnopix.com/ https://www.pldrive.de/ We prefer WordPress designs, created with the plugin ELEMENTOR, so that we can easily edit the content by ourselves. The final design should look professional, competent and modern.

Target Market(s)

With our website, we want to reach the following target groups. <br> <br> <br> <br> <br> <br> <br> <br> <br> <br> <br> <br> <br> <br> <br> <br> <br> <br> <br> <br> <br> <br> <br> <br> <br> <br> <br> <br> <br> <br> <br> <br> <br> <br> <br> <br> <br> <br> <br> <br> <br> <br> <br> <br> <br> <br> <br> <br> <br>

Industry/Entity Type

Consulting

Logo Text

(optionally) VelmaTrix

Font styles to use
Sans Serif

Colors

Designer to choose colors to be used in the design.

Requirements
Must have
• 1. Outsourcing 3. Development 4. Business Analyst 5. Training • Partners • Careers • About Us 1. Project A 2. Project B 3. Project C • Contact The above-mentioned background picture with nature motifs (mountains, lakes, rivers, forests, etc.). WordPress design in primary colors blue and green.
Nice to have
• ELEMENTOR template. Effects for the background pictures. Counter of all successful projects for Output Management, Business Analyst and Training

```html
<!DOCTYPE html>
<html lang="en">
<head>
<meta charset="utf-8">
<title>VelmaTrix – Output Management</title>
<link href="https://fonts.googleapis.com/css2?family=Montserrat:wght@300;400;500&family=Open+Sans:wght@400;600;700&display=swap" rel="stylesheet">
<style>
:root{
  --green:#2fa84f;
  --green-bright:#39b54a;
  --green-deep:#1f8f5a;
  --teal:#1d8a78;
  --ink:#333333;
  --ink-soft:#555555;
  --mist:#e9e4df;
  --footer:#333333;
  --white:#ffffff;
  --field:rgba(255,255,255,0.35);
}
*{box-sizing:border-box;margin:0;padding:0}
html,body{width:1200px;height:4975px;overflow:hidden}
body{position:relative;font-family:"Montserrat",sans-serif;color:var(--ink);background:var(--white)}
.abs{position:absolute}
section,header,footer{position:absolute;left:0;width:1200px;overflow:hidden}
h2{font-family:"Open Sans",sans-serif;font-weight:700;font-size:26px;letter-spacing:.5px}

/* hero */
.hero{top:0;height:800px;background:linear-gradient(160deg,#1b8c78 0%,#26a06a 45%,#36b04e 100%)}
.hero-scene{position:absolute;inset:0;background:
  linear-gradient(180deg,rgba(255,255,255,0) 0%,rgba(255,255,255,.08) 30%,rgba(0,40,30,.12) 45%,rgba(255,255,255,.06) 70%,rgba(0,0,0,0) 100%)}
.brand{display:flex;align-items:center;gap:12px;font-family:"Montserrat",sans-serif;font-weight:300;color:var(--white);font-size:20px}
.brand-square{width:22px;height:22px;background:var(--white)}
.hero .brand{left:110px;top:60px}
.nav{right:100px;top:66px;display:flex;gap:32px;font-size:13px;color:var(--white)}
.hero-kicker{left:108px;top:466px;width:150px;height:40px;transform-origin:0 0;transform:rotate(-90deg) translate(-150px,0);
  font-family:"Open Sans",sans-serif;font-weight:600;font-size:38px;line-height:40px;color:var(--white);letter-spacing:1px}
.hero-title{left:149px;top:578px;font-family:"Open Sans",sans-serif;font-weight:600;font-size:38px;color:var(--white);letter-spacing:.5px}
.hero-text{left:112px;top:634px;width:420px;font-size:15px;line-height:22px;color:rgba(255,255,255,.9);font-weight:300}

/* services */
.services{top:800px;height:605px;background:var(--white)}
.section-icon{position:absolute;left:50%;transform:translateX(-50%)}
.services h2{position:absolute;top:98px;width:100%;text-align:center}
.service{position:absolute;width:285px;border-left:2px solid var(--green);padding-left:12px}
.service svg{display:block;margin-bottom:4px}
.service h3{font-family:"Montserrat",sans-serif;font-weight:400;font-size:18px;line-height:21px;margin-bottom:12px}
.service p{font-size:11.5px;line-height:18px;color:var(--ink-soft)}

/* benefits */
.benefits{top:1405px;height:556px;background:linear-gradient(180deg,#dfe4e6 0%,#f3e9e1 35%,#e6e5e0 60%,#c9cfcf 100%)}
.benefits-kicker{left:108px;top:88px;width:88px;height:34px;transform-origin:0 0;transform:rotate(-90deg) translate(-88px,0);
  font-family:"Open Sans",sans-serif;font-weight:700;font-size:32px;line-height:34px;color:var(--green)}
.benefits-title{left:147px;top:75px;font-family:"Open Sans",sans-serif;font-weight:700;font-size:22px;line-height:24px;color:#2d2d2d}
.benefit{position:absolute;font-size:20px;line-height:22px;color:#4a4a4a;font-weight:400}
.benefit::before{content:"";display:block;width:86px;height:8px;border-radius:4px;background:var(--green);margin-bottom:12px}
.benefit.right{text-align:right}
.benefit.right::before{margin-left:auto}
.benefit.center{text-align:center}
.benefit.center::before{margin:0 auto 12px}

/* partners */
.partners{top:1961px;height:497px;background:var(--white)}
.partners h2{position:absolute;top:85px;width:100%;text-align:center}
.partners-text{position:absolute;top:176px;width:100%;text-align:center;font-size:16.5px;line-height:22.5px;color:#444}
.badge{position:absolute;top:388px;background:#d3d3d3}

/* career */
.career{top:2458px;height:473px;background:linear-gradient(135deg,#1e9e50 0%,#28ac4b 50%,#1c9d55 100%)}
.career-line{left:112px;width:2px;background:var(--white)}
.career h2{position:absolute;left:129px;top:162px;color:var(--white);font-size:25px}
.career-text{left:129px;top:232px;width:950px;font-size:16.5px;line-height:22.5px;color:var(--white)}

/* about */
.about{top:2931px;height:1043px;background:var(--white)}
.about h2{position:absolute;top:76px;width:100%;text-align:center}
.about-text{position:absolute;top:120px;width:100%;text-align:center;font-size:16.5px;line-height:22.5px;color:#444}
.team{position:absolute;left:112px;top:185px;width:986px;height:858px;display:grid;grid-template-columns:repeat(3,1fr);grid-template-rows:repeat(2,1fr)}
.portrait{position:relative}
.p1{background:linear-gradient(180deg,#1c1c1c,#3a3a3a)}
.p2{background:linear-gradient(180deg,#e9e9e9,#b9b9b9)}
.p3{background:linear-gradient(180deg,#4f5f4e,#2e3a2c)}
.p4{background:linear-gradient(180deg,#7fa6c4,#c8d6df)}
.p5{background:linear-gradient(180deg,#252525,#3b3b3b)}
.p6{background:linear-gradient(180deg,#45c2e8,#1f9ed3)}
.caption{position:absolute;left:0;right:0;bottom:0;height:152px;background:rgba(60,60,60,.92);color:var(--white);padding:44px 20px 0 20px}
.caption::before{content:"";display:block;width:14px;height:1px;background:var(--white);margin-bottom:6px}
.caption h4{font-family:"Montserrat",sans-serif;font-weight:500;font-size:16px;margin-bottom:6px}
.caption p{font-size:9px;line-height:12px;width:240px;color:#ddd}

/* contact */
.contact{top:3974px;height:717px;background:linear-gradient(180deg,#6e9a55 0%,#3f6f39 45%,#5e8c3c 80%,#9fbd52 100%)}
.contact-panel{position:absolute;left:124px;top:72px;width:952px;height:568px;background:linear-gradient(180deg,#3cb54b 0%,#2aa556 45%,#18876d 100%)}
.contact h2{position:absolute;top:86px;width:100%;text-align:center;color:var(--white);font-size:25px}
.field{position:absolute;left:133px;width:686px;height:33px;background:var(--field);color:var(--white);font-size:14px;text-align:center;line-height:33px}
.field.area{height:172px;line-height:33px}
.send{position:absolute;left:382px;top:512px;width:170px;height:32px;border-radius:16px;background:var(--white);color:#222;font-size:13px;font-weight:500;text-align:center;line-height:32px}

/* footer */
.site-footer{top:4691px;height:284px;background:var(--footer);color:var(--white)}
.site-footer .brand{position:absolute;left:50%;top:60px;transform:translateX(-50%);font-size:20px;color:var(--green-bright)}
.site-footer .brand-square{background:var(--green-bright);width:30px;height:30px}
.footer-links{left:129px;top:130px;font-size:12.5px;line-height:19.5px;list-style:none}
.footer-copy{left:350px;width:500px;top:142px;text-align:center;font-size:12.5px;line-height:19.5px}
.socials{left:980px;top:151px;display:flex;gap:12px}
.socials span{width:16px;height:16px;border-radius:50%;background:var(--white)}
</style>
</head>
<body>

<header class="hero">
  <div class="hero-scene" role="img" aria-label="Mountain lake valley photograph under a green colour wash"></div>
  <div class="brand abs"><span class="brand-square"></span>VelmaTrix</div>
  <nav class="nav abs"><span>Services</span><span>Our Partners</span><span>Careers</span><span>About Us</span></nav>
  <div class="hero-kicker abs">OUTPUT</div>
  <h1 class="hero-title abs">MANAGEMENT</h1>
  <p class="hero-text abs">Lorem ipsum dolor sit amet, consectetur adipiscing elit, sed do eiusmod tempor incididunt ut labore et dolore magna aliqua. Lacus luctus accumsan tortor posuere ac ut consequat semper viverra.</p>
</header>

<section class="services">
  <svg class="section-icon" style="top:54px" width="40" height="40" viewBox="0 0 40 40" fill="none" stroke="#2fa84f" stroke-width="2.5" stroke-linecap="round"><path d="M6 34 L30 10"/><path d="M34 34 L10 10"/><circle cx="32" cy="8" r="5"/><circle cx="8" cy="8" r="4"/></svg>
  <h2>OUR SERVICES</h2>

  <article class="service" style="left:104px;top:153px">
    <svg width="22" height="22" viewBox="0 0 22 22" fill="none" stroke="#2fa84f" stroke-width="1.6"><rect x="2" y="5" width="14" height="14" rx="2"/><path d="M9 12 L19 3 M14 3 h5 v5"/></svg>
    <h3>Output<br>Management System</h3>
    <p>Lorem ipsum dolor sit amet, consectetur adipiscing elit. Maecenas vel convallis lectus, at lacinia dolor. Donec molestie tellus id nisi aliquet lobortis. Vestibulum ultricies justo in augue consectetur pretium.</p>
  </article>
  <article class="service" style="left:479px;top:153px">
    <svg width="22" height="22" viewBox="0 0 22 22" fill="none" stroke="#2fa84f" stroke-width="1.6"><circle cx="11" cy="7" r="4"/><path d="M3 20 c0-5 16-5 16 0"/></svg>
    <h3>Outsourcing<br>&amp; Freelancing</h3>
    <p>Praesent lacinia hendrerit sem, et aliquet dui convallis at. Quisque convallis mi eu purus pretium vehicula. Phasellus vel mollis lectus. Sed sed dignissim urna. In sit amet neque at ante accumsan sollicitudin.</p>
  </article>
  <article class="service" style="left:819px;top:153px">
    <svg width="22" height="22" viewBox="0 0 22 22" fill="none" stroke="#2fa84f" stroke-width="1.6"><circle cx="14" cy="7" r="5"/><circle cx="7" cy="13" r="3"/><path d="M2 21 c0-4 10-4 10 0"/></svg>
    <h3>Business<br>Analysts</h3>
    <p>Lorem ipsum dolor sit amet, consectetur adipiscing elit. Maecenas vel convallis lectus, at lacinia dolor. Donec molestie tellus id nisi aliquet lobortis. Vestibulum ultricies justo in augue consectetur pretium.</p>
  </article>
  <article class="service" style="left:346px;top:370px">
    <svg width="22" height="22" viewBox="0 0 22 22" fill="none" stroke="#2fa84f" stroke-width="1.6"><circle cx="11" cy="8" r="6"/><path d="M11 14 v7 M7 21 h8"/></svg>
    <h3>Front-End<br>Development</h3>
    <p>Lorem ipsum dolor sit amet, consectetur adipiscing elit. Maecenas vel convallis lectus, at lacinia dolor. Donec molestie tellus id nisi aliquet lobortis. Vestibulum ultricies justo in augue consectetur pretium.</p>
  </article>
  <article class="service" style="left:703px;top:370px">
    <svg width="22" height="22" viewBox="0 0 22 22" fill="none" stroke="#2fa84f" stroke-width="1.6"><rect x="2" y="2" width="18" height="12"/><circle cx="8" cy="17" r="2"/><path d="M4 21 c0-2 8-2 8 0"/></svg>
    <h3>Training<br>Programme</h3>
    <p>Praesent lacinia hendrerit sem, et aliquet dui convallis at. Quisque convallis mi eu purus pretium vehicula. Phasellus vel mollis lectus. Sed sed dignissim urna. In sit amet neque at ante accumsan sollicitudin.</p>
  </article>
</section>

<section class="benefits" role="img" aria-label="Misty mountain lake at sunrise photograph">
  <div class="benefits-kicker abs">OMS</div>
  <h2 class="benefits-title abs">BENEFITS OF<br>OUT<br>MANAGEMENT SYSTEM</h2>
  <p class="benefit" style="left:110px;top:218px">OMS Simplifies and Accelerates<br>External Communication</p>
  <p class="benefit right" style="right:100px;top:218px">Helps Reduce<br>Communication Mistakes</p>
  <p class="benefit" style="left:110px;top:328px">Provides Customers With Fast<br>and Secure Responses<br>&nbsp;to your questions</p>
  <p class="benefit right" style="right:100px;top:328px">Employees can focus<br>on the essential as they can access<br>prepared templates</p>
  <p class="benefit center" style="left:350px;width:500px;top:445px">Companies get complete transparency<br>about their communication</p>
</section>

<section class="partners">
  <svg class="section-icon" style="top:40px" width="58" height="36" viewBox="0 0 58 36" fill="none" stroke="#2fa84f" stroke-width="2.5" stroke-linejoin="round"><path d="M2 6 h10 v20 h-10 M56 6 h-10 v20 h10"/><path d="M12 10 l10-4 l14 8 l-8 4 M46 10 l-10 -4 M12 24 l12 8 l22 -8"/></svg>
  <h2>OUR PARTNERS</h2>
  <p class="partners-text">Lorem ipsum dolor sit amet, consectetur adipiscing elit. Maecenas vel convallis lectus, at lacinia dolor.<br>Donec molestie tellus id nisi aliquet lobortis. Vestibulum ultricies justo in augue consectetur pretium. Praesent lacinia<br>hendrerit sem, et aliquet dui convallis at. Quisque convallis mi eu purus pretium vehicula.<br>Phasellus vel mollis lectus. Sed sed dignissim urna.<br>In sit amet neque at ante accumsan sollicitudin.</p>
  <div class="badge" style="left:182px;width:60px;height:60px;top:385px"></div>
  <div class="badge" style="left:350px;width:58px;height:60px;top:385px"></div>
  <div class="badge" style="left:487px;width:52px;height:52px;top:388px;border-radius:50%"></div>
  <div class="badge" style="left:600px;width:84px;height:52px;top:392px"></div>
  <div class="badge" style="left:738px;width:110px;height:52px;top:392px"></div>
  <div class="badge" style="left:898px;width:64px;height:66px;top:386px;border-radius:50%"></div>
  <div class="badge" style="left:1005px;width:60px;height:14px;top:410px;border-radius:7px"></div>
</section>

<section class="career" role="img" aria-label="Desk workspace with laptop and keyboard photograph under a green colour wash">
  <div class="career-line abs" style="top:130px;height:60px"></div>
  <svg class="abs" style="left:129px;top:132px" width="38" height="24" viewBox="0 0 38 24" fill="none" stroke="#ffffff" stroke-width="2"><path d="M2 22 h34 M6 22 v-8 M13 22 v-14 M20 22 v-10 M27 22 v-16 M34 22 v-6"/></svg>
  <h2>CAREER</h2>
  <div class="career-line abs" style="top:226px;height:112px"></div>
  <p class="career-text abs">Lorem ipsum dolor sit amet, consectetur adipiscing elit. Maecenas vel convallis lectus, at lacinia dolor.<br>Donec molestie tellus id nisi aliquet lobortis. Vestibulum ultricies justo in augue consectetur pretium. Praesent lacinia<br>hendrerit sem, et aliquet dui convallis at. Quisque convallis mi eu purus pretium vehicula.<br>Phasellus vel mollis lectus. Sed sed dignissim urna.<br>In sit amet neque at ante accumsan sollicitudin.</p>
</section>

<section class="about">
  <svg class="section-icon" style="top:44px" width="40" height="30" viewBox="0 0 40 30" fill="none" stroke="#2fa84f" stroke-width="2"><circle cx="10" cy="10" r="4"/><circle cx="20" cy="7" r="5"/><circle cx="30" cy="10" r="4"/><path d="M2 28 v-6 h36 v6 M10 22 v6 M20 22 v6 M30 22 v6"/></svg>
  <h2>ABOUT US</h2>
  <p class="about-text">Neque egestas congue quisque egestas diam in arcu cursus euismod. Odio eu feugiat<br>pretium nibh ipsum consequat nisl vel pretium. Velit laoreet id donec ultrices.</p>
  <div class="team">
    <div class="portrait p1" role="img" aria-label="Black and white portrait of a team member"></div>
    <div class="portrait p2" role="img" aria-label="Portrait of a team member against a patterned wall">
      <div class="caption"><h4>John Doe</h4><p>Netus et malesuada fames ac turpis. Elementum sagittis vitae et leo duis ut diam.</p></div>
    </div>
    <div class="portrait p3" role="img" aria-label="Portrait of a team member outdoors"></div>
    <div class="portrait p4" role="img" aria-label="Portrait of a team member by the sea"></div>
    <div class="portrait p5" role="img" aria-label="Black and white portrait of a team member"></div>
    <div class="portrait p6" role="img" aria-label="Portrait of a team member against a blue wall"></div>
  </div>
</section>

<section class="contact" role="img" aria-label="Green rolling hills landscape photograph">
  <form class="contact-panel">
    <svg class="section-icon" style="top:44px" width="40" height="34" viewBox="0 0 40 34" fill="none" stroke="#ffffff" stroke-width="2" stroke-linejoin="round"><path d="M2 14 L38 2 L28 32 L18 20 Z M18 20 L38 2"/></svg>
    <h2>CONTACT US</h2>
    <div class="field" style="top:122px">Name</div>
    <div class="field" style="top:180px">Email</div>
    <div class="field" style="top:239px">Topic</div>
    <div class="field area" style="top:297px">Description</div>
    <div class="send">Send</div>
  </form>
</section>

<footer class="site-footer">
  <div class="brand"><span class="brand-square"></span>VelmaTrix</div>
  <ul class="footer-links abs"><li>Home</li><li>Our Policy</li><li>Terms &amp; Conditions</li><li>Blog</li><li>About Us</li></ul>
  <p class="footer-copy abs">© 2019 Tarnopix Technologies GmbH<br>Lorem ipsum dolor sit amet, consectetur adipiscing elit,<br>sed do eiusmod tempor incididunt ut labore et dolore magna aliqua.<br>Ut tortor pretium viverra suspendisse potenti nullam.</p>
  <div class="socials abs"><span></span><span></span><span></span></div>
</footer>

</body>
</html>
```